Business card design for holistic health care clinic

We need a double-sided business card design for our holistic health care clinic that integrates our logo design and also its color scheme. My business is called Valmira. It is an integrative medicine clinic. You have already done the logo for me. Please ensure an elegant and upscale design that is not cluttered, but still has all the necessary information (please see below for details).

Target Market(s)

Wellness, fitness, rehabilitation for educated, well-traveled open-minded clients who are focused on natural, organic, balanced and preventive healthcare and lifestyle.

Industry/Entity Type

Medical

Contact Information for Business Card

Modern, clean.

Number of Pages Required

1 page

Font styles to use
Serif
Sans Serif

Colors

Designer to choose colors to be used in the design.

Requirements
Must have
• Logo on one side, all other information on the other side.
• Other information should include:
• Tobias Wrenfeld - DOE, CPT, LMT
• 4100 East Marrow Drive
• Austin, TX 78119
• 512 555 0148
• 818 555 0192
• info@ValmiraHealth.example
• t.wrenfeld@ValmiraHealth.example
Nice to have
• Darker background on front - but not totally black - shaded/dark gray.

```html
<!DOCTYPE html>
<html lang="en">
<head>
<meta charset="utf-8">
<title>Valmira – Business Card</title>
<link href="https://fonts.googleapis.com/css2?family=Maven+Pro:wght@500;700&family=Roboto:wght@400&family=Roboto+Condensed:wght@400;700&display=swap" rel="stylesheet">
<style>
  :root{
    --backdrop:#d6d7d9;
    --card-dark:#262729;
    --card-mid:#333437;
    --brand-blue:#1d93d2;
    --band-blue:#1a8ccc;
    --text-light:#f2f2f2;
    --text-soft:#e4e4e4;
  }
  *{margin:0;padding:0;box-sizing:border-box}
  html,body{width:1200px;height:901px;overflow:hidden;background:var(--backdrop)}
  .card{
    position:absolute;left:100px;top:163px;width:1000px;height:575px;
    border-radius:22px;overflow:hidden;
    background:linear-gradient(135deg,var(--card-mid) 0%,var(--card-dark) 55%,#1f2022 100%);
    box-shadow:0 10px 30px rgba(0,0,0,.25);
    font-family:"Roboto",sans-serif;color:var(--text-light);
  }
  .brand{position:absolute;left:56px;top:108px}
  .brand-name{
    font-family:"Maven Pro",sans-serif;font-weight:700;font-size:86px;line-height:1;
    letter-spacing:1px;color:var(--brand-blue);
  }
  .brand-tagline{
    font-family:"Maven Pro",sans-serif;font-weight:500;font-size:26px;
    color:var(--brand-blue);margin-top:4px;margin-left:4px;
  }
  .address{position:absolute;left:58px;top:280px;font-size:25px;line-height:30px;color:var(--text-soft)}
  .contacts{position:absolute;left:58px;top:356px;list-style:none}
  .contacts li{display:flex;align-items:center;height:31px;font-size:25px;color:var(--text-soft)}
  .contacts svg{width:21px;height:21px;margin-right:18px;fill:var(--brand-blue);flex:none}
  .person{
    position:absolute;right:60px;top:368px;
    font-family:"Roboto Condensed",sans-serif;color:var(--brand-blue);white-space:nowrap;
  }
  .person-name{font-weight:700;font-size:34px;letter-spacing:.5px}
  .person-credentials{font-size:22px;margin-left:6px}
  .slogan-band{
    position:absolute;left:0;bottom:0;width:100%;height:50px;background:var(--band-blue);
    display:flex;align-items:center;padding-left:58px;font-size:25px;color:#fff;
  }
</style>
</head>
<body>
  <div class="card">
    <div class="brand">
      <div class="brand-name">VALMIRA</div>
      <div class="brand-tagline">Integrative Holistic Medicine</div>
    </div>

    <div class="address">
      <div>4100 East Marrow Drive</div>
      <div>Austin, TX 78119</div>
    </div>

    <ul class="contacts">
      <li>
        <svg viewBox="0 0 24 24" aria-hidden="true"><path d="M6.6 10.8a15.2 15.2 0 0 0 6.6 6.6l2.2-2.2c.3-.3.7-.4 1-.2 1.1.4 2.3.6 3.6.6.6 0 1 .4 1 1V20c0 .6-.4 1-1 1A17 17 0 0 1 3 4c0-.6.4-1 1-1h3.5c.6 0 1 .4 1 1 0 1.3.2 2.5.6 3.6.1.3 0 .7-.2 1z"/></svg>
        512 555 0148
      </li>
      <li>
        <svg viewBox="0 0 24 24" aria-hidden="true"><path d="M7 1h10a2 2 0 0 1 2 2v18a2 2 0 0 1-2 2H7a2 2 0 0 1-2-2V3a2 2 0 0 1 2-2zm0 3v14h10V4zm5 15.3a1 1 0 1 0 0 2 1 1 0 0 0 0-2z"/></svg>
        818 555 0192
      </li>
      <li>
        <svg viewBox="0 0 24 24" aria-hidden="true"><path d="M2 5h20v14H2zm2 2v.5l8 5 8-5V7zm0 2.9V17h16V9.9l-8 5z"/></svg>
        t.wrenfeld@ValmiraHealth.example
      </li>
      <li>
        <svg viewBox="0 0 24 24" aria-hidden="true"><path d="M12 2a10 10 0 1 0 0 20 10 10 0 0 0 0-20zm6.9 6h-3a15.6 15.6 0 0 0-1.3-3.6A8 8 0 0 1 18.9 8zM12 4c.8 1.2 1.5 2.5 1.9 4h-3.8c.4-1.5 1.1-2.8 1.9-4zM4.3 14a8 8 0 0 1 0-4h3.4a16 16 0 0 0 0 4zm.8 2h3a15.6 15.6 0 0 0 1.3 3.6A8 8 0 0 1 5.1 16zm3-8h-3a8 8 0 0 1 4.3-3.6C8.8 5.5 8.4 6.7 8.1 8zM12 20c-.8-1.2-1.5-2.5-1.9-4h3.8c-.4 1.5-1.1 2.8-1.9 4zm2.3-6H9.7a14.6 14.6 0 0 1 0-4h4.6a14.6 14.6 0 0 1 0 4zm.3 5.6c.6-1.1 1-2.3 1.3-3.6h3a8 8 0 0 1-4.3 3.6zm1.7-5.6a16 16 0 0 0 0-4h3.4a8 8 0 0 1 0 4z"/></svg>
        www.ValmiraHealth.example
      </li>
    </ul>

    <div class="person">
      <span class="person-name">TOBIAS WRENFELD</span><span class="person-credentials">- DOE, CPT, LMT</span>
    </div>

    <div class="slogan-band">centered on you – your wellbeing, your own goals</div>
  </div>
</body>
</html>
```